Crestline Staffing PEO - Web Build for Professional Employment Organization

We need a website built for our new PEO (professional employment organization). This company will offer third party Human Resource services to companies who are looking to outsource:<br/>Recruiting<br/>Administrative Onboarding<br/>New hire training, ongoing training and development<br/>Payroll/compensation processing/services<br/>Employee Relations<br/>Unemployment Claim Facilitation<br/>Benefits Plans and Administration<br/><br/>I have attached the logo below. Please use that as a reference and color match as best as possible. <br/><br/>Here are some of the competitor's websites:<br/>https://www.velmorahr.com/ <br/>https://www.trundelpay.com/<br/>https://www.trundelpay.com/<br/>https://www.qzn.com/<br/>https://www.bremwickhr.com/<br/>https://orvalepeo.com/contact-orvale/<br/><br/>

Target Market(s)

Startups and mid-sized businesses

Number of Pages Required

5+ page

Font styles to use
Sans Serif

Colors
0592cd

Requirements
Must have
• Features Pages
• SEO driven keyword rich content
• Strong focus on our ability to provide unemployment claim facilitation services as well as mandatory training/certification fulfillment
Nice to have
• I'd like to see one mockup with a Live Chat version if possible. In theory, the Live Chat messages would go directly to our front desk person.

```html
<!DOCTYPE html>
<html lang="en">
<head>
<meta charset="utf-8">
<title>Crestline Staffing PEO – Professional Employment Organization</title>
<link href="https://fonts.googleapis.com/css2?family=Lato:wght@400;700;900&display=swap" rel="stylesheet">
<style>
:root{
  --teal:#1b8fa6;
  --teal-dark:#157c91;
  --navy:#2f4a66;
  --navy-deep:#2c3f57;
  --ink:#333d47;
  --text:#555e66;
  --light:#f1f2f3;
  --white:#ffffff;
}
*{margin:0;padding:0;box-sizing:border-box}
html,body{width:1200px;height:3662px;overflow:hidden;background:var(--white)}
body{font-family:'Lato',sans-serif;color:var(--text);position:relative}
.abs{position:absolute}
.c{text-align:center}
.btn{position:absolute;background:var(--teal);color:var(--white);font-weight:700;font-size:14px;display:flex;align-items:center;justify-content:center;letter-spacing:.3px}
.h-sec{position:absolute;left:0;width:1200px;text-align:center;font-weight:900;font-size:26px;color:var(--ink)}

/* header */
.topbar{left:825px;top:0;width:375px;height:44px;background:var(--navy-deep);clip-path:polygon(0 0,100% 0,100% 100%,18px 100%);color:var(--white);font-size:16px;font-weight:700;display:flex;align-items:center;padding-left:37px}
.brand{display:flex;align-items:center;gap:10px;color:var(--navy);font-weight:900;font-size:24px}
.brand .dot{width:26px;height:26px;border-radius:50%;background:var(--teal)}
.nav a{position:absolute;top:81px;font-size:14px;font-weight:700;color:var(--ink);text-decoration:none}
.nav a.active{color:var(--teal)}
.nav .underline{position:absolute;left:447px;top:106px;width:67px;height:3px;background:var(--teal)}
.login{left:1041px;top:74px;width:87px;height:34px;border:2px solid var(--teal);color:var(--teal);font-size:14px;font-weight:700;display:flex;align-items:center;justify-content:center}

/* hero */
.hero{left:0;top:131px;width:1200px;height:546px;background:linear-gradient(180deg,#8d8a86 0%,#6d6258 45%,#4a3c33 100%)}
.hero h1{position:absolute;left:0;width:1200px;top:209px;text-align:center;color:var(--white);font-size:40px;font-weight:900}
.hero p{position:absolute;left:200px;width:800px;top:263px;text-align:center;color:var(--white);font-size:25px;line-height:39px}
.dots{left:569px;top:489px;display:flex;gap:10px}
.dots span{width:10px;height:10px;border-radius:50%;background:var(--white)}
.dots span:first-child{background:var(--teal)}

/* services */
.services{left:0;top:1059px;width:1200px;height:633px;background:var(--navy)}
.svc-label{position:absolute;color:var(--white);font-size:18px;font-weight:700;line-height:25px}

/* resources */
.card{left:74px;top:1752px;width:333px;height:435px;border:2px solid #d8dcdf;background:var(--white)}
.ph{position:absolute}
.item-title{position:absolute;left:705px;width:420px;font-size:18px;font-weight:900;color:var(--ink);line-height:27px}
.item-text{position:absolute;left:705px;width:420px;font-size:14px;line-height:23px}

/* testimonial */
.testi{left:0;top:2242px;width:1200px;height:307px;background:linear-gradient(90deg,#1b8fa6 0%,#25718d 55%,#30486a 100%)}

/* news */
.news{position:absolute;width:331px;height:400px;text-align:center}
.news .date{position:absolute;top:210px;left:0;width:100%;color:var(--teal);font-size:14px}
.news h3{position:absolute;top:236px;left:40px;width:251px;font-size:17px;font-weight:700;color:var(--ink);line-height:26px}
.news p{position:absolute;top:298px;left:0;width:100%;font-size:14px;line-height:25px;padding:0 8px}
.news a{position:absolute;top:380px;width:100%;left:0;color:var(--teal);font-weight:700;font-size:14px;text-decoration:none}

/* partners */
.partners{left:0;top:3117px;width:1200px;height:179px;background:var(--light)}
.partner{position:absolute;top:96px;display:flex;align-items:center;gap:8px;font-size:30px;font-weight:700;color:var(--ink);transform:translateX(-50%)}
.partner i{width:30px;height:30px;border-radius:50%;background:var(--teal);display:block}

/* footer */
.footer{left:0;top:3296px;width:1200px;height:309px;background:#f6f6f6}
.f-title{position:absolute;top:58px;color:var(--teal);font-size:16px;font-weight:700}
.f-list{position:absolute;font-size:13px;color:var(--ink);list-style:none}
.bottombar{left:0;top:3605px;width:1200px;height:57px;background:var(--navy-deep);color:#d7dde3;font-size:12px}
.social{position:absolute;top:19px;width:20px;height:20px;border-radius:50%;background:var(--white)}
</style>
</head>
<body>

<!-- header -->
<div class="abs topbar">Call us Toll-Free: 1-800-555-0142</div>
<div class="abs brand" style="left:74px;top:54px"><span class="dot"></span>Crestline Staffing PEO</div>
<nav class="nav">
  <a class="active" style="left:460px">HOME</a>
  <a style="left:536px">ABOUT US</a>
  <a style="left:641px">SERVICES</a>
  <a style="left:740px">BLOG</a>
  <a style="left:811px">RESOURCES</a>
  <a style="left:927px">CONTACT US</a>
  <span class="underline"></span>
</nav>
<div class="abs login">LOG IN</div>

<!-- hero -->
<section class="abs hero" role="img" aria-label="Photo of a business team meeting around a table">
  <h1>PROFESSIONAL EMPLOYMENT ORGANIZATION</h1>
  <p>Suspendisse tempor vel libero et vehicula. In at risus id<br>elit vehicula convallis.</p>
  <div class="abs dots"><span></span><span></span><span></span><span></span></div>
</section>

<!-- welcome -->
<span class="abs" style="left:587px;top:736px;width:26px;height:26px;border-radius:50%;background:var(--teal)"></span>
<h2 class="h-sec" style="top:786px">WELCOME TO OUR WEBSITE</h2>
<p class="abs c" style="left:80px;width:1043px;top:834px;font-size:15px;line-height:25px">Aliquam molestie, mi et imperdiet euismod, dui purus auctor tellus, et interdum lacus lectus et ante. Sed accumsan sollicitudin sapien, sit amet adipiscing turpis gravida ac. In congue, neque ac lobortis volutpat, libero mauris varius mi, vitae suscipit ipsum ligula vitae risus. Duis aliquam nibh a dui iaculis viverra id a velit. Vivamus egestas risus in magna varius commodo. Sed semper viverra egestas.</p>
<div class="btn" style="left:525px;top:940px;width:150px;height:45px">READ MORE</div>

<!-- services -->
<section class="abs services">
  <h2 class="h-sec" style="top:67px;color:var(--white);font-size:24px">OUR SERVICES</h2>
  <svg class="abs" style="left:0;top:0" width="1200" height="633" viewBox="0 0 1200 633">
    <g stroke="#c8d2dc" stroke-width="2" fill="none">
      <polyline points="441,177 486,177 512,228"/>
      <polyline points="759,177 714,177 688,228"/>
      <line x1="389" y1="280" x2="496" y2="280"/>
      <line x1="811" y1="280" x2="704" y2="280"/>
      <polyline points="441,384 486,384 512,332"/>
      <polyline points="759,384 714,384 688,332"/>
      <line x1="600" y1="384" x2="600" y2="415"/>
    </g>
    <circle cx="600" cy="280" r="104" fill="var(--teal)"/>
    <circle cx="600" cy="280" r="90" fill="#ffffff"/>
    <g font-family="Lato, sans-serif" font-weight="900" fill="var(--teal)" text-anchor="middle">
      <text x="600" y="264" font-size="24">Crestline</text>
      <text x="600" y="292" font-size="20">Staffing</text>
      <text x="600" y="318" font-size="20">PEO</text>
    </g>
    <g fill="var(--teal)" stroke="#ffffff" stroke-width="2">
      <circle cx="405" cy="177" r="36"/>
      <circle cx="353" cy="280" r="36"/>
      <circle cx="405" cy="384" r="36"/>
      <circle cx="795" cy="177" r="36"/>
      <circle cx="847" cy="280" r="36"/>
      <circle cx="795" cy="384" r="36"/>
      <circle cx="600" cy="451" r="36"/>
    </g>
    <g fill="none" stroke="#ffffff" stroke-width="2" stroke-linecap="round" stroke-linejoin="round">
      <!-- recruiting: magnifier over person -->
      <circle cx="400" cy="172" r="10"/><line x1="407" y1="179" x2="418" y2="190"/>
      <circle cx="400" cy="169" r="3"/><path d="M394 178c2-4 10-4 12 0"/>
      <!-- onboarding: group -->
      <circle cx="353" cy="270" r="5"/><path d="M343 292c0-8 20-8 20 0"/>
      <circle cx="338" cy="276" r="4"/><path d="M330 292c0-6 8-8 12-6"/>
      <circle cx="368" cy="276" r="4"/><path d="M376 292c0-6-8-8-12-6"/>
      <!-- employee relations: two people -->
      <circle cx="396" cy="371" r="5"/><path d="M388 398v-14h16v14"/>
      <circle cx="414" cy="371" r="5"/><path d="M406 398v-14h16v14"/>
      <!-- payroll: document with coin -->
      <rect x="782" y="162" width="26" height="22" rx="2"/><line x1="787" y1="169" x2="803" y2="169"/><line x1="787" y1="175" x2="799" y2="175"/>
      <circle cx="786" cy="188" r="7" fill="var(--teal)"/><line x1="786" y1="184" x2="786" y2="192"/>
      <!-- unemployment claim: person with tie -->
      <circle cx="847" cy="270" r="7"/><path d="M834 296c0-10 26-10 26 0z"/><path d="M847 284l-2 6 2 3 2-3z"/>
      <!-- benefits: clipboard with tick -->
      <rect x="783" y="368" width="24" height="30" rx="2"/><rect x="790" y="364" width="10" height="6" rx="1"/>
      <polyline points="788,384 793,389 802,378"/>
      <!-- training: certificate -->
      <rect x="586" y="436" width="28" height="22" rx="2"/><line x1="591" y1="443" x2="609" y2="443"/><line x1="591" y1="449" x2="602" y2="449"/>
      <circle cx="609" cy="459" r="5" fill="var(--teal)"/><path d="M606 463l-2 7 5-3 5 3-2-7"/>
    </g>
  </svg>
  <div class="svc-label" style="right:857px;top:165px;text-align:right">Recruiting</div>
  <div class="svc-label" style="right:906px;top:255px;text-align:right">Administrative<br>Onboarding</div>
  <div class="svc-label" style="right:857px;top:372px;text-align:right">Employee Relations</div>
  <div class="svc-label" style="left:856px;top:152px">Payroll/compensation<br>processing/services</div>
  <div class="svc-label" style="left:908px;top:256px">Unemployment Claim<br>Facilitation</div>
  <div class="svc-label" style="left:856px;top:361px">Benefits Plans and<br>Administration</div>
  <div class="svc-label c" style="left:400px;width:400px;top:502px">New hire training, ongoing training<br>and development</div>
</section>

<!-- resources -->
<div class="abs card">
  <div class="ph" style="left:0;top:0;width:329px;height:196px;background:linear-gradient(135deg,#cfd5d8,#7a7f83)" role="img" aria-label="Photo of a presenter at a whiteboard"></div>
  <h3 class="abs" style="left:19px;top:212px;font-size:26px;font-weight:900;color:var(--ink)">RESOURCES</h3>
  <p class="abs" style="left:21px;top:254px;width:280px;font-size:14px;line-height:23px">Euismod, dui purus auctor tellus, et interdum lacus lectus et ante accumsan sollicitudin sapien, sit ame neque ac lobortis..</p>
  <div class="btn" style="left:21px;top:359px;width:152px;height:47px">READ MORE</div>
</div>

<div class="ph" style="left:434px;top:1753px;width:243px;height:186px;background:linear-gradient(135deg,#4a4d50,#d9dadb)" role="img" aria-label="Photo of a claim form beside a laptop"></div>
<h3 class="item-title" style="top:1745px">UNEMPLOYMENT CLAIM FACILITATION SERVICES</h3>
<p class="item-text" style="top:1805px">Euismod, dui purus auctor tellus, et interdum lacus lectus et ante. Sed accumsan sollicitudin sapien, sit ame neque ac lobortis porttitor nec lectus...</p>
<div class="btn" style="left:705px;top:1892px;width:152px;height:47px">READ MORE</div>

<div class="abs" style="left:434px;top:1970px;width:692px;height:2px;background:#d8dcdf"></div>

<div class="ph" style="left:434px;top:2000px;width:243px;height:187px;background:linear-gradient(135deg,#9aa6b0,#3d4650)" role="img" aria-label="Photo of a training session in a meeting room"></div>
<h3 class="item-title" style="top:1994px">MANDATORY TRAINING/CERTIFICATION FULFILLMENT</h3>
<p class="item-text" style="top:2054px">Euismod, dui purus auctor tellus, et interdum lacus lectus et ante. Sed accumsan sollicitudin sapien, sit ame neque ac lobortis porttitor nec lectus...</p>
<div class="btn" style="left:705px;top:2141px;width:152px;height:47px">READ MORE</div>

<!-- testimonial -->
<section class="abs testi">
  <h2 class="h-sec" style="top:42px;color:var(--white);font-size:24px">SEE WHAT OUR CLIENTS ARE SAYING ABOUT US</h2>
  <svg class="abs" style="left:115px;top:153px" width="24" height="30" viewBox="0 0 24 30"><polyline points="18,3 6,15 18,27" fill="none" stroke="#fff" stroke-width="4"/></svg>
  <svg class="abs" style="left:1063px;top:153px" width="24" height="30" viewBox="0 0 24 30"><polyline points="6,3 18,15 6,27" fill="none" stroke="#fff" stroke-width="4"/></svg>
  <div class="abs" style="left:164px;top:104px;width:128px;height:128px;border-radius:50%;background:#d9d3cc;border:4px solid #ffffff" role="img" aria-label="Client portrait"></div>
  <p class="abs" style="left:343px;top:99px;width:690px;color:var(--white);font-size:14px;line-height:26px">“ Aliquam molestie, mi et imperdiet euismod, dui purus auctor tellus, et interdum lacus lectus et ante. Sed accumsan sollicitudin sapien, sit amet adipiscing turpis gravida ac. In congue, neque ac lobortis volutpat, libero mauris varius mi, vitae suscipit ipsum ligula vitae risus aptent taciti sociosqu ad litora torquent per conubia nostra, per inceptos himenaeos...”</p>
  <div class="abs" style="left:343px;top:213px;color:var(--white);font-size:14px;font-weight:700">NAME HEADING</div>
</section>

<!-- what's new -->
<h2 class="h-sec" style="top:2589px">WHAT’S NEW</h2>
<article class="news" style="left:75px;top:2653px">
  <div class="ph" style="left:0;top:0;width:331px;height:181px;background:linear-gradient(135deg,#c7ccd0,#55606a)" role="img" aria-label="Photo of colleagues shaking hands in an office"></div>
  <div class="date">January 25, 2020</div><h3>ALIQUAM MOLESTIE MI ET IMPERDIET</h3>
  <p>Euismod, dui purus auctor tellus, et interdum lacus lectus et ante. Sed accumsan sollicitudin sapien, sit ame neque ac lobortis..</p><a>Read More</a>
</article>
<article class="news" style="left:434px;top:2653px">
  <div class="ph" style="left:0;top:0;width:331px;height:181px;background:linear-gradient(135deg,#d8dde2,#2f3a48)" role="img" aria-label="Photo of a hand selecting a candidate profile"></div>
  <div class="date">January 25, 2020</div><h3>ALIQUAM MOLESTIE MI ET IMPERDIET</h3>
  <p>Euismod, dui purus auctor tellus, et interdum lacus lectus et ante. Sed accumsan sollicitudin sapien, sit ame neque ac lobortis..</p><a>Read More</a>
</article>
<article class="news" style="left:798px;top:2653px">
  <div class="ph" style="left:0;top:0;width:331px;height:181px;background:linear-gradient(135deg,#b9b6b1,#3f4349)" role="img" aria-label="Photo of a business handshake at a meeting"></div>
  <div class="date">January 25, 2020</div><h3>ALIQUAM MOLESTIE MI ET IMPERDIET</h3>
  <p>Euismod, dui purus auctor tellus, et interdum lacus lectus et ante. Sed accumsan sollicitudin sapien, sit ame neque ac lobortis..</p><a>Read More</a>
</article>

<!-- partners -->
<section class="abs partners">
  <h2 class="h-sec" style="top:40px;font-size:18px;font-weight:700;color:var(--navy)">PARTNERS</h2>
  <div class="partner" style="left:284px"><i></i>Brightwell</div>
  <div class="partner" style="left:493px"><i></i>Oakmere</div>
  <div class="partner" style="left:690px"><i></i>Tallis</div>
  <div class="partner" style="left:900px"><i></i>Norvane</div>
</section>

<!-- footer -->
<footer class="abs footer">
  <div class="abs brand" style="left:74px;top:78px;font-size:20px"><span class="dot" style="width:22px;height:22px"></span>Crestline Staffing PEO</div>
  <p class="abs" style="left:74px;top:144px;width:230px;font-size:13px;line-height:23px;color:var(--ink)">Vestibulum ante ipsum primis in faucibus orci luctus et ultrices posuere cubilia aliquam nibh a dui iaculis viverra id a velit..</p>
  <div class="abs" style="left:74px;top:242px;font-size:13px;font-weight:700;color:var(--teal)">Read More</div>

  <div class="f-title" style="left:354px">QUICK LINKS</div>
  <ul class="f-list" style="left:354px;top:88px;line-height:30.8px"><li>Home</li><li>About Us</li><li>Services</li><li>Blog</li><li>Resources</li><li>Contact Us</li></ul>

  <div class="f-title" style="left:533px">RESOURCES</div>
  <ul class="f-list" style="left:533px;top:94px;line-height:27.7px"><li>Vestibulum ante ipsum</li><li>Primis in faucibus orci</li><li>Luctus et ultrice</li><li>Posuere cubilia</li></ul>

  <div class="f-title" style="left:734px">QUICK LINKS</div>
  <ul class="f-list" style="left:734px;top:94px;line-height:27.7px"><li>Vestibulum ante ipsum</li><li>Primis in faucibus orci</li><li>Luctus et ultrice</li><li>Posuere cubilia</li></ul>

  <div class="f-title" style="left:934px">CONTACT INFO</div>
  <p class="abs" style="left:934px;top:94px;font-size:13px;line-height:24px;color:var(--ink)">417 Harlow Lane<br>Brookfield, BK2 7QT</p>
  <svg class="abs" style="left:934px;top:148px" width="12" height="12" viewBox="0 0 24 24"><path d="M6 2l4 4-2 3c1 3 4 6 7 7l3-2 4 4-3 4C10 22 2 14 2 5z" fill="var(--teal)"/></svg>
  <div class="abs" style="left:967px;top:146px;font-size:13px;color:var(--ink)">1-800-555-0142</div>
  <svg class="abs" style="left:934px;top:177px" width="13" height="10" viewBox="0 0 26 20"><rect width="26" height="20" rx="2" fill="var(--teal)"/><polyline points="1,2 13,11 25,2" fill="none" stroke="#f6f6f6" stroke-width="2"/></svg>
  <div class="abs" style="left:967px;top:174px;font-size:13px;color:var(--ink)">info@crestlinepeo.com</div>
</footer>

<div class="abs bottombar">
  <div class="abs" style="left:74px;top:21px">Copyright © 2020 Crestline Staffing PEO. All Right Reserved</div>
  <span class="social" style="left:938px"></span>
  <span class="social" style="left:978px"></span>
  <span class="social" style="left:1020px"></span>
  <span class="social" style="left:1063px"></span>
  <span class="social" style="left:1106px"></span>
</div>

</body>
</html>
```